Boutique custom software development company needs new business card

Our nearly 20 year old custom software development company would like to better include the fact that we are now providing Bitcoin services. These new services are B2B include education (how to acquire and securely hold Bitcoin) and integrating Bitcoin payments into existing ecommerce sites or other existing systems. Please keep the card clean and simple. Attached is our current design and some other files. vextorial.com

Target Market(s)

businesses owners interested in long term relationship

Industry/Entity Type

Custom software development and Bitcoin

Contact Information for Business Card

Dale Parker, dale@vextorial.com, vextorial.com, (888) 555-VXTRL

Font styles to use
Other font styles liked:
• monospace

Requirements
Must have
• double-sided
Nice to have
• clean and simple
Should not have
• physical address

```html
<!DOCTYPE html>
<html lang="en">
<head>
<meta charset="utf-8">
<title>Vextorial – Business Card</title>
<link rel="stylesheet" href="https://fonts.googleapis.com/css2?family=Courier+Prime:wght@400;700&family=Montserrat:wght@300;700&display=swap">
<style>
  :root {
    --backdrop: #474747;
    --card: #161616;
    --edge-blue: #3d72bc;
    --brand-blue: #3f74c0;
    --accent-orange: #f07a22;
    --ink-white: #f2f2f2;
    --emboss-grey: #8a8a8a;
  }
  * { box-sizing: border-box; margin: 0; padding: 0; }
  html, body {
    width: 1200px; height: 801px; overflow: hidden;
    background: var(--backdrop);
  }
  .canvas { position: relative; width: 1200px; height: 801px; }
  .card {
    position: absolute; top: 246px;
    width: 540px; height: 309px;
    background: var(--card);
    border-radius: 18px;
    border-bottom: 3px solid var(--edge-blue);
    box-shadow: 0 14px 30px rgba(0,0,0,0.45);
    overflow: hidden;
  }
  .card--front { left: 30px; }
  .card--back { left: 630px; }

  /* Front */
  .brand-lockup {
    position: absolute; left: 40px; top: 76px;
    display: flex; align-items: center; gap: 12px;
  }
  .brand-square {
    width: 34px; height: 34px;
    background: var(--accent-orange);
  }
  .wordmark {
    font-family: "Montserrat", sans-serif; font-weight: 700;
    font-size: 40px; letter-spacing: -1px; line-height: 1;
    color: var(--brand-blue);
  }
  .tagline {
    position: absolute; left: 42px; top: 124px;
    font-family: "Montserrat", sans-serif; font-weight: 300;
    font-size: 16px; color: var(--brand-blue);
  }
  .accent-bar {
    position: absolute; left: 0; top: 170px;
    width: 16px; height: 38px;
    background: var(--accent-orange);
  }
  .person-name {
    position: absolute; left: 34px; top: 166px;
    font-family: "Courier Prime", monospace; font-weight: 700;
    font-size: 26px; line-height: 1.2; color: var(--accent-orange);
  }
  .rule {
    position: absolute; left: 214px; right: 0; top: 183px;
    height: 1.5px; background: var(--accent-orange);
  }
  .person-title {
    position: absolute; left: 34px; top: 196px;
    font-family: "Courier Prime", monospace;
    font-size: 14px; color: var(--ink-white);
  }
  .contact-list {
    position: absolute; left: 34px; top: 228px;
    list-style: none;
    font-family: "Courier Prime", monospace;
    font-size: 13px; line-height: 19px; color: var(--ink-white);
  }
  .contact-list li { display: flex; align-items: center; gap: 8px; }
  .contact-list svg { width: 12px; height: 12px; fill: var(--accent-orange); }
  .services {
    position: absolute; right: 32px; top: 206px;
    list-style: none; text-align: right;
    font-family: "Courier Prime", monospace;
    font-size: 13px; line-height: 18px; color: var(--ink-white);
  }
  .services .services-head { color: var(--accent-orange); font-weight: 700; }

  /* Back */
  .back-lockup {
    position: absolute; left: 0; right: 0; top: 96px;
    text-align: center;
  }
  .back-wordmark {
    font-family: "Montserrat", sans-serif; font-weight: 700;
    font-size: 68px; letter-spacing: -2px; line-height: 1;
    color: var(--emboss-grey);
  }
  .back-tagline {
    margin-top: 10px;
    font-family: "Montserrat", sans-serif; font-weight: 300;
    font-size: 24px; color: var(--emboss-grey);
  }
</style>
</head>
<body>
<main class="canvas">

  <section class="card card--front" aria-label="Card front">
    <div class="brand-lockup">
      <div class="brand-square"></div>
      <div class="wordmark">VEXTORIAL</div>
    </div>
    <div class="tagline">developer of custom applications</div>

    <div class="accent-bar"></div>
    <h1 class="person-name">Dale Parker</h1>
    <div class="rule"></div>
    <p class="person-title">Founding Partner</p>

    <ul class="contact-list">
      <li>
        <svg viewBox="0 0 24 24" aria-hidden="true"><path d="M6.6 10.8a15.1 15.1 0 0 0 6.6 6.6l2.2-2.2c.3-.3.7-.4 1-.2 1.1.4 2.3.6 3.6.6.6 0 1 .4 1 1V20c0 .6-.4 1-1 1A17 17 0 0 1 3 4c0-.6.4-1 1-1h3.5c.6 0 1 .4 1 1 0 1.3.2 2.5.6 3.6.1.3 0 .7-.2 1z"/></svg>
        (888) 555-VXTRL
      </li>
      <li>
        <svg viewBox="0 0 24 24" aria-hidden="true"><path d="M2 5h20v14H2z M2 5l10 8 10-8" fill="none" stroke="#f07a22" stroke-width="2.5"/></svg>
        dale@vextorial.com
      </li>
      <li>
        <svg viewBox="0 0 24 24" aria-hidden="true"><circle cx="12" cy="12" r="10" fill="none" stroke="#f07a22" stroke-width="2.5"/><path d="M2 12h20M12 2c3 3 3 17 0 20M12 2c-3 3-3 17 0 20" fill="none" stroke="#f07a22" stroke-width="2"/></svg>
        www.vextorial.com
      </li>
    </ul>

    <ul class="services">
      <li class="services-head">Bitcoin Services</li>
      <li>B2B education</li>
      <li>secure custody</li>
      <li>payment integration</li>
    </ul>
  </section>

  <section class="card card--back" aria-label="Card back">
    <div class="back-lockup">
      <div class="back-wordmark">VEXTORIAL</div>
      <div class="back-tagline">developer of custom applications</div>
    </div>
  </section>

</main>
</body>
</html>
```